Interval Timer App

Need to have design for the attached wireframe. Similar app can be found here: https://shop.lumaverse.net/store/apps/details?id=cc.quillfern.pulseclock

```html
<!DOCTYPE html>
<html lang="en">
<head>
<meta charset="utf-8">
<title>Interval Timer – Settings</title>
<link href="https://fonts.googleapis.com/css2?family=Montserrat:wght@400;500;600&display=swap" rel="stylesheet">
<style>
  :root{
    --bg:#f7f8fa;
    --ink:#2b2c38;
    --muted:#5f6170;
    --blue:#3579d2;
    --blue-dark:#1c3d6e;
    --card:#ffffff;
    --line:#e4e6ea;
    --track:#eef0f4;
    --scrim:rgba(0,0,0,0.2);
  }
  *{margin:0;padding:0;box-sizing:border-box}
  html,body{width:675px;height:1200px;overflow:hidden}
  body{background:var(--bg);font-family:"Montserrat",sans-serif;color:var(--ink);position:relative}
  .screen{position:absolute;inset:0}
  .heading{position:absolute;left:0;width:675px;text-align:center;font-weight:500}
  .sets-title{top:90px;font-size:38px}
  .work-title{top:284px;font-size:41px}
  .rest-title{top:662px;font-size:41px}
  .stepper-btn{position:absolute;top:177px;width:66px;height:43px;border-radius:18px;background:var(--blue)}
  .stepper-btn svg{position:absolute;left:50%;top:50%;transform:translate(-50%,-50%)}
  .stepper-minus{left:202px}
  .stepper-plus{left:409px}
  .stepper-value{position:absolute;top:176px;left:0;width:675px;text-align:center;font-size:38px;color:var(--muted)}
  .picker-card{position:absolute;left:81px;width:515px;background:var(--card);border-radius:10px;box-shadow:0 3px 12px rgba(0,0,0,0.12);overflow:hidden}
  .work-card{top:356px;height:274px}
  .rest-card{top:733px;height:300px}
  .picker-label{position:absolute;left:0;width:100%;text-align:center;font-size:24px;color:var(--muted)}
  .picker-row{position:absolute;left:0;width:100%;height:64px}
  .num{position:absolute;top:0;width:64px;height:64px;margin-left:-32px;line-height:64px;text-align:center;font-size:30px;color:var(--muted)}
  .num.selected{background:var(--blue);color:#fff;border-radius:50%}
  .f1{opacity:.75}.f2{opacity:.55}.f3{opacity:.3}
  .scrim{position:absolute;inset:0;background:var(--scrim)}
  .sheet{position:absolute;left:0;top:891px;width:675px;height:309px;background:#fff;border-radius:26px 26px 0 0}
  .free-row{position:absolute;top:0;left:0;width:100%;height:95px;border-bottom:2px solid var(--line)}
  .free-icon{position:absolute;left:32px;top:24px}
  .free-label{position:absolute;left:120px;top:32px;font-size:26px;font-weight:500}
  .toggle{position:absolute;left:540px;top:29px;width:103px;height:38px;border-radius:19px;background:var(--track)}
  .toggle-knob{position:absolute;left:8px;top:8px;width:22px;height:22px;border-radius:50%;background:var(--blue-dark)}
  .action{position:absolute;top:120px;width:180px;margin-left:-90px;text-align:center}
  .action svg{display:block;margin:0 auto}
  .action-label{display:block;margin-top:10px;font-size:22px;font-weight:500}
</style>
</head>
<body>
<div class="screen">
  <h2 class="heading sets-title">Sets</h2>
  <div class="stepper-btn stepper-minus"><svg width="24" height="24" viewBox="0 0 24 24"><path d="M3 12h18" stroke="#fff" stroke-width="4" stroke-linecap="round"/></svg></div>
  <div class="stepper-value">3</div>
  <div class="stepper-btn stepper-plus"><svg width="24" height="24" viewBox="0 0 24 24"><path d="M3 12h18M12 3v18" stroke="#fff" stroke-width="4" stroke-linecap="round"/></svg></div>

  <h2 class="heading work-title">Work Interval</h2>
  <div class="picker-card work-card">
    <div class="picker-label" style="top:10px">Minutes</div>
    <div class="picker-row" style="top:58px">
      <span class="num f3" style="left:-7px">58</span>
      <span class="num" style="left:33px">59</span>
      <span class="num" style="left:140px;margin-left:-92px">1</span>
      <span class="num" style="left:163px">2</span>
      <span class="num selected" style="left:256px">3</span>
      <span class="num" style="left:304px">4</span>
      <span class="num f1" style="left:350px">5</span>
      <span class="num f2" style="left:393px">6</span>
      <span class="num f3" style="left:434px">7</span>
    </div>
    <div class="picker-label" style="top:146px">Seconds</div>
    <div class="picker-row" style="top:193px">
      <span class="num f3" style="left:-6px">11</span>
      <span class="num f1" style="left:69px">12</span>
      <span class="num" style="left:127px">13</span>
      <span class="num" style="left:185px">14</span>
      <span class="num selected" style="left:256px">15</span>
      <span class="num" style="left:326px">16</span>
      <span class="num" style="left:388px">17</span>
      <span class="num f2" style="left:450px">18</span>
      <span class="num f3" style="left:512px">19</span>
    </div>
  </div>

  <h2 class="heading rest-title">Rest Interval</h2>
  <div class="picker-card rest-card">
    <div class="picker-label" style="top:10px">Minutes</div>
    <div class="picker-row" style="top:56px">
      <span class="num f2" style="left:50px">57</span>
      <span class="num" style="left:114px">58</span>
      <span class="num" style="left:180px">59</span>
      <span class="num selected" style="left:256px">1</span>
      <span class="num" style="left:322px">2</span>
      <span class="num" style="left:375px">3</span>
      <span class="num f1" style="left:421px">4</span>
      <span class="num f3" style="left:468px">5</span>
    </div>
    <div class="picker-label" style="top:140px">Seconds</div>
  </div>
</div>

<div class="scrim"></div>

<div class="sheet">
  <div class="free-row">
    <svg class="free-icon" width="50" height="50" viewBox="0 0 50 50" fill="none" stroke="#1f2030" stroke-width="2.4" stroke-linecap="round">
      <circle cx="27" cy="28" r="15"/>
      <path d="M23 8h8M27 8v5M38 14l3-3M27 28l6-7"/>
      <path d="M4 22h7M2 29h8M5 36h7"/>
    </svg>
    <span class="free-label">Free time mode</span>
    <div class="toggle"><span class="toggle-knob"></span></div>
  </div>

  <div class="action" style="left:131px">
    <svg width="50" height="50" viewBox="0 0 50 50" fill="none" stroke="#3579d2" stroke-width="2.4" stroke-linejoin="round" stroke-linecap="round">
      <path d="M6 19h8l11-9v30l-11-9H6z"/>
      <path d="M31 19c3 3 3 9 0 12M36 14c6 6 6 16 0 22"/>
    </svg>
    <span class="action-label">Sound</span>
  </div>

  <div class="action" style="left:336px">
    <svg width="54" height="54" viewBox="0 0 54 54" fill="none" stroke="#3579d2" stroke-width="2.4" stroke-linejoin="round" stroke-linecap="round">
      <rect x="17" y="8" width="20" height="38" rx="3" transform="rotate(-30 27 27)"/>
      <path d="M8 16l-3 5M10 22l-3 5M46 32l3-5M44 38l3-5"/>
    </svg>
    <span class="action-label">Vibration</span>
  </div>

  <div class="action" style="left:544px">
    <svg width="54" height="54" viewBox="0 0 54 54" fill="none" stroke="#3579d2" stroke-width="2.4" stroke-linejoin="round" stroke-linecap="round">
      <path d="M9 8h36a3 3 0 0 1 3 3v24a3 3 0 0 1-3 3H24l-9 8v-8H9a3 3 0 0 1-3-3V11a3 3 0 0 1 3-3z"/>
      <path d="M27 31l-8-8a4.5 4.5 0 0 1 8-5 4.5 4.5 0 0 1 8 5z"/>
    </svg>
    <span class="action-label">Feedback</span>
  </div>
</div>
</body>
</html>
```